Rework Front of Food Packaging

We are a herbal coffee company that sells a tea that tastes like coffee - tovalinea.com. We love our current packaging, but want a total refresh on it.

The items we want to see on the front:
Keep the leaf pattern in the design
We still want to see a coffee cup.
3 icons - AIP friendly, Prebiotic and Caffeine-free
Tag line: Steeps like tea, tastes like coffee
text: Restorative Herbal Coffee
Text: Light Roast

I want to see some fresh. We use the herbs dandelion root, Carob and Chicory root in the blend so seeing the herbs on the front would be good. Some ideas of what I like:

https://images.brindlecove-cdn.net/content/v1/5cc89bc4a09a7e73d8882ea7/1564711566898-36HFNRLIZ85OVSRP3AU1/6-07_Frivano_Strawberry-Lifestyle_Composite.jpg?format=2500w

https://ii.quellbarrow.com/fcgi-bin/iipsrv.fcgi?FIF=/images/quellbarrow/source/39802_XXX_v1.tif&wid=480&cvt=jpeg
Updates

Designs look the same

Requirements
Must have
• see above
Nice to have
• Please keep the same color packaging
Should not have
• I want photos of the cup, herbs. I do not want graphics of these items

```html
<!DOCTYPE html>
<html lang="en">
<head>
<meta charset="utf-8">
<title>Tovalinea Light Roast – Pouch Front</title>
<link rel="stylesheet" href="https://fonts.googleapis.com/css2?family=Amatic+SC:wght@700&family=Cabin:wght@500;700&family=Allura&display=swap">
<style>
  :root {
    --backdrop: #f8efe1;
    --pouch-top: #eccb9f;
    --pouch-mid: #f0b39f;
    --pouch-low: #ee9f98;
    --pouch-base: #e88a8b;
    --seal: #e3c08f;
    --roast: #a5402d;
    --banner: #f2c241;
    --banner-edge: #e6ad2c;
    --ink: #3a2418;
    --white: #ffffff;
    --logo-gold: #f0b93c;
    --badge-pink: #eb8c86;
  }
  * { box-sizing: border-box; margin: 0; padding: 0; }
  html, body { width: 1200px; height: 789px; overflow: hidden; }
  body { background: var(--backdrop); position: relative; }

  .pouch {
    position: absolute; left: 375px; top: 35px;
    width: 450px; height: 720px;
    background: linear-gradient(180deg, var(--pouch-top) 0%, var(--pouch-mid) 45%, var(--pouch-low) 75%, var(--pouch-base) 100%);
    border-radius: 6px 6px 14px 14px;
    overflow: hidden;
  }
  .pouch__seal {
    position: absolute; left: 0; top: 0; width: 100%; height: 22px;
    background: var(--seal);
  }
  .pouch__wave {
    position: absolute; left: 0; bottom: 0; width: 100%; height: 60px;
  }

  .brand {
    position: absolute; left: 160px; top: 50px;
    width: 130px; height: 130px;
    background: var(--white);
    border-radius: 36px;
    transform: rotate(45deg);
  }
  .brand__name {
    position: absolute; left: 160px; top: 50px;
    width: 130px; height: 130px;
    display: flex; align-items: center; justify-content: center;
    font-family: "Cabin", sans-serif; font-weight: 700;
    font-size: 23px; color: var(--logo-gold); letter-spacing: 0.5px;
  }

  .hero-photo {
    position: absolute; left: 50px; top: 205px;
    width: 335px; height: 210px;
    border-radius: 40px;
    background:
      radial-gradient(ellipse 38% 40% at 45% 30%, #b98a78 0%, #c99582 60%, transparent 100%),
      radial-gradient(ellipse 50% 25% at 50% 80%, #7b3a24 0%, #9a6a52 60%, transparent 100%),
      radial-gradient(ellipse 20% 25% at 80% 70%, #8c8de8 0%, transparent 100%);
  }

  .servings {
    position: absolute; left: 341px; top: 253px;
    width: 54px; height: 54px; border-radius: 50%;
    background: var(--badge-pink);
    border: 2px solid #f4c2b8;
    color: var(--white);
    font-family: "Cabin", sans-serif; text-align: center;
    display: flex; flex-direction: column; justify-content: center;
  }
  .servings__label { font-size: 6px; letter-spacing: 1px; line-height: 1; }
  .servings__count { font-size: 17px; font-weight: 700; line-height: 1.05; }

  .product-name {
    position: absolute; left: 0; top: 410px; width: 100%;
    text-align: center;
    font-family: "Amatic SC", sans-serif; font-weight: 700;
    font-size: 86px; line-height: 1; color: var(--roast);
    letter-spacing: 1px;
  }

  .descriptor {
    position: absolute; left: 58px; top: 506px;
    width: 335px; height: 33px;
    background: var(--banner);
    border: 2px solid var(--banner-edge);
    clip-path: polygon(3% 0, 97% 0, 100% 50%, 97% 100%, 3% 100%, 0 50%);
    display: flex; align-items: center; justify-content: center;
    font-family: "Cabin", sans-serif; font-weight: 700;
    font-size: 18px; letter-spacing: 0.6px; color: var(--ink);
  }

  .tagline {
    position: absolute; left: 0; top: 545px; width: 100%;
    text-align: center;
    font-family: "Allura", cursive;
    font-size: 36px; line-height: 1; color: var(--white);
  }

  .claims {
    position: absolute; left: 103px; top: 592px;
    display: flex; gap: 12px;
  }
  .claims__icon {
    width: 52px; height: 52px; border-radius: 50%;
    border: 2.5px solid var(--white);
    background: rgba(255,255,255,0.12);
    display: flex; flex-direction: column; align-items: center; justify-content: center;
    font-family: "Cabin", sans-serif; font-weight: 700;
    color: var(--white); text-align: center; line-height: 1.05;
  }
  .claims__big { font-size: 16px; letter-spacing: 0.5px; }
  .claims__small { font-size: 7px; letter-spacing: 0.6px; }
  .claims__icon--brew {
    background: var(--banner); border-color: #f6d978; color: var(--ink);
  }
  .claims__icon--brew .claims__small { font-size: 6.5px; letter-spacing: 0.3px; }

  .net-weight {
    position: absolute; left: 140px; top: 655px;
    width: 170px; height: 18px;
    border: 1.5px solid var(--white); border-radius: 10px;
    display: flex; align-items: center; justify-content: center;
    font-family: "Cabin", sans-serif; font-weight: 500;
    font-size: 9.5px; color: var(--white); letter-spacing: 0.3px;
  }
</style>
</head>
<body>
  <main class="pouch">
    <div class="pouch__seal"></div>
    <svg class="pouch__wave" viewBox="0 0 450 60" preserveAspectRatio="none" aria-hidden="true">
      <path d="M0 30 C120 5 300 55 450 20 L450 60 L0 60 Z" fill="#e98f8f" opacity="0.6"/>
    </svg>

    <div class="hero-photo" role="img" aria-label="Photo of a steaming cup of herbal coffee with dandelion root, chicory root and blue chicory flowers"></div>

    <div class="brand"></div>
    <div class="brand__name">Tovalinea</div>

    <div class="servings">
      <span class="servings__label">SERVINGS</span>
      <span class="servings__count">15</span>
      <span class="servings__label">SERVINGS</span>
    </div>

    <h1 class="product-name">LIGHT ROAST</h1>
    <div class="descriptor">RESTORATIVE HERBAL COFFEE</div>
    <p class="tagline">Steeps like tea, tastes like coffee</p>

    <div class="claims">
      <div class="claims__icon">
        <span class="claims__big">AIP</span>
        <span class="claims__small">FRIENDLY</span>
      </div>
      <div class="claims__icon">
        <span class="claims__small">PRE-</span>
        <span class="claims__small">BIOTIC</span>
      </div>
      <div class="claims__icon">
        <span class="claims__small">CAFFEINE</span>
        <span class="claims__small">FREE</span>
      </div>
      <div class="claims__icon claims__icon--brew">
        <span class="claims__small">FRENCH</span>
        <span class="claims__small">PRESS OR</span>
        <span class="claims__small">DRIP BAG</span>
      </div>
    </div>

    <div class="net-weight">NET WT 4 OZ (0.25 LB) 113 kg</div>
  </main>
</body>
</html>
```